Business Card Design Project

We need a Business Card for an Mechanical Engineering firm in Singapore. The design should be Modern & Technical looking, yet eye catching.

Our company deals in Cutting Tools & Machine Accessories for the Manufacturing Industries such as Oil & Gas, Aero Space, etc... For more information on our Company, you can either email me or view our website www.torvalen.com.sg.

We are trying to revamp our image to give our consumers a fresh new perspective to our company, so we welcome all ideas.

Industry/Entity Type

Business

Requirements
Must have
• Must incorporate New Company Logo into the card as shown in Uploaded file.

```html
<!DOCTYPE html>
<html lang="en">
<head>
<meta charset="utf-8">
<title>Torvalen Tools — Business Card</title>
<link rel="stylesheet" href="https://fonts.googleapis.com/css2?family=PT+Sans:ital,wght@0,400;0,700;1,400&display=swap">
<style>
  :root {
    --backdrop: #a9a9a9;
    --card-black: #1c1819;
    --card-white: #ffffff;
    --brand-red: #8e1b20;
    --bright-red: #b3262c;
    --ink: #2a2a2a;
    --silver-light: #f2f2f2;
    --silver-dark: #8c8c8c;
    --text-font: "PT Sans", Arial, sans-serif;
  }
  * { box-sizing: border-box; margin: 0; padding: 0; }
  html, body {
    width: 1200px; height: 951px; overflow: hidden;
    background: var(--backdrop);
    font-family: var(--text-font);
  }
  .canvas { position: relative; width: 1200px; height: 951px; }

  .card {
    position: absolute; width: 620px; height: 354px;
    border-radius: 22px; overflow: hidden;
    box-shadow: 0 8px 22px rgba(0,0,0,.25);
  }

  /* Front */
  .card-front { left: 80px; top: 90px; background: var(--card-black); }
  .front-edge { position: absolute; top: 0; width: 620px; height: 354px; }
  .front-brand {
    position: absolute; left: 0; right: 0; top: 130px;
    display: flex; justify-content: center; align-items: center; gap: 14px;
  }
  .brand-dot { width: 30px; height: 30px; border-radius: 50%; background: var(--bright-red); }
  .front-brand .brand-name {
    color: #ffffff; font-weight: 700; font-size: 44px; letter-spacing: 1px;
  }
  .front-url {
    position: absolute; left: 0; right: 0; top: 232px; text-align: center;
    color: #ffffff; font-size: 19px; letter-spacing: .5px;
  }

  /* Back */
  .card-back { left: 500px; top: 500px; background: var(--card-white); }
  .back-brand {
    position: absolute; left: 42px; top: 72px;
    display: flex; align-items: center; gap: 10px;
  }
  .back-brand .brand-dot { width: 22px; height: 22px; }
  .back-brand .brand-name {
    color: var(--brand-red); font-weight: 700; font-size: 28px; letter-spacing: .5px;
  }
  .person { position: absolute; left: 42px; top: 178px; }
  .person-name { color: var(--ink); font-size: 22px; }
  .person-role { color: var(--bright-red); font-size: 17px; font-style: italic; }

  .contact-list {
    position: absolute; left: 350px; top: 52px; list-style: none;
    color: var(--ink); font-size: 17px; line-height: 23px;
  }
  .contact-list li { display: flex; align-items: center; gap: 8px; }
  .contact-list svg { width: 13px; height: 13px; fill: var(--brand-red); flex: none; }
  .contact-list .web span { color: var(--bright-red); }
  .address {
    position: absolute; left: 350px; top: 178px;
    display: flex; gap: 8px; color: var(--ink); font-size: 17px; line-height: 22px;
  }
  .address svg { width: 14px; height: 14px; fill: var(--brand-red); margin-top: 3px; flex: none; }
  .back-swoosh { position: absolute; left: 0; bottom: 0; width: 620px; height: 120px; }
</style>
</head>
<body>
<main class="canvas">

  <section class="card card-front" aria-label="Card front">
    <svg class="front-edge" viewBox="0 0 620 354" aria-hidden="true">
      <defs>
        <linearGradient id="silver" x1="0" x2="1">
          <stop offset="0" stop-color="var(--silver-dark)"/>
          <stop offset=".5" stop-color="var(--silver-light)"/>
          <stop offset="1" stop-color="var(--silver-dark)"/>
        </linearGradient>
      </defs>
      <path d="M0 0 H40 Q24 177 40 354 H0 Z" fill="url(#silver)"/>
      <path d="M40 0 Q24 177 40 354" stroke="var(--bright-red)" stroke-width="4" fill="none"/>
      <path d="M620 0 H580 Q596 177 580 354 H620 Z" fill="url(#silver)"/>
      <path d="M580 0 Q596 177 580 354" stroke="var(--bright-red)" stroke-width="4" fill="none"/>
    </svg>
    <div class="front-brand">
      <span class="brand-dot"></span>
      <span class="brand-name">TORVALEN TOOLS</span>
    </div>
    <p class="front-url">www.torvalentools.com</p>
  </section>

  <section class="card card-back" aria-label="Card back">
    <div class="back-brand">
      <span class="brand-dot"></span>
      <span class="brand-name">TORVALEN TOOLS</span>
    </div>

    <div class="person">
      <p class="person-name">Marcus Lindqvel</p>
      <p class="person-role">manager</p>
    </div>

    <ul class="contact-list">
      <li><svg viewBox="0 0 16 16"><path d="M4 1 L6.5 4.5 L5 6.5 Q7 10 9.5 11 L11.5 9.5 L15 12 L13 15 Q5 14 1 3 Z"/></svg>512-555-0140</li>
      <li><svg viewBox="0 0 16 16"><rect x="3" y="1" width="10" height="14" rx="2"/></svg>512-555-0141</li>
      <li><svg viewBox="0 0 16 16"><path d="M1 3 H15 V13 H1 Z"/></svg>info@torvalentools.com</li>
      <li class="web"><svg viewBox="0 0 16 16"><circle cx="8" cy="8" r="7"/></svg>www.<span>torvalentools</span>.com</li>
    </ul>

    <div class="address">
      <svg viewBox="0 0 16 16"><path d="M8 1 L15 8 H13 V15 H3 V8 H1 Z"/></svg>
      <p>1480 Calder Hill Rd.<br>Brenton, TX 78110</p>
    </div>

    <svg class="back-swoosh" viewBox="0 0 620 120" preserveAspectRatio="none" aria-hidden="true">
      <path d="M0 40 Q260 20 620 70 V120 H0 Z" fill="var(--card-black)"/>
      <path d="M0 80 Q300 40 620 36 V120 H0 Z" fill="var(--brand-red)"/>
      <path d="M0 100 Q330 70 620 78 V120 H0 Z" fill="var(--bright-red)"/>
    </svg>
  </section>

</main>
</body>
</html>
```